Modern Business Card for Larkwell 2018

Our company assumes the best about people. We are creating an online community of entrepreneurs and business leaders who struggle with marketing their business online.

This business card should POP! We recently got a new logo and are launching a new website next month, so our business cards should make a statement that feels:
-Fresh
-Smart
-Trustworthy
-Fun

Target Market(s)

small business owners, entrepreneurs

Industry/Entity Type

Digital Marketing

Contact Information for Business Card

Dimensions: 3.5" x 2"

Font styles to use
Sans Serif

Colors
f37122
ffffff

Requirements
Must have
• We need a business card with a modern, bold design. We will use one side of the card as a lead-generation offer, so text on one side will need to fit up to 140 characters. The business card should stick to our core colors (orange, black, and white).
Nice to have
• We think a vertical "portrait" design could be interesting.
Should not have
• Should not look like a traditional business card. The round icon should stand out from a distance.

```html
<!DOCTYPE html>
<html lang="en">
<head>
<meta charset="utf-8">
<title>Larkwell Business Card</title>
<link href="https://fonts.googleapis.com/css2?family=Open+Sans:wght@400;600;700;800&display=swap" rel="stylesheet">
<style>
  :root {
    --orange: #f37122;
    --orange-deep: #e85d1c;
    --orange-light: #f8963a;
    --white: #ffffff;
    --ink: #1c1c1c;
    --stage: #2a2a2c;
    --rule: #8a8a8a;
  }
  * { box-sizing: border-box; margin: 0; padding: 0; }
  html, body { width: 1200px; height: 900px; overflow: hidden; }
  body {
    background: var(--stage);
    font-family: "Open Sans", Arial, sans-serif;
    position: relative;
  }
  .card {
    position: absolute;
    left: 250px;
    width: 700px;
    height: 400px;
    border-radius: 6px;
    overflow: hidden;
    box-shadow: 0 10px 30px rgba(0,0,0,.45);
  }
  /* Lead-generation side */
  .card--offer {
    top: 30px;
    background: linear-gradient(110deg, var(--orange-light) 0%, var(--orange) 45%, var(--orange-deep) 100%);
    color: var(--white);
  }
  .offer__brand {
    position: absolute;
    left: 40px; top: 60px;
    width: 200px;
    display: flex; flex-direction: column; align-items: center; gap: 14px;
  }
  .offer__dot {
    width: 120px; height: 120px; border-radius: 50%;
    background: var(--white);
  }
  .offer__name {
    font-weight: 800; font-size: 30px; letter-spacing: .5px; color: var(--white);
  }
  .offer__divider {
    position: absolute; left: 268px; top: 34px;
    width: 1px; height: 190px; background: rgba(255,255,255,.55);
  }
  .offer__copy { position: absolute; left: 300px; top: 34px; width: 370px; }
  .offer__headline {
    font-weight: 800; font-size: 27px; line-height: 1.02; text-transform: uppercase;
  }
  .offer__text {
    margin-top: 12px; font-size: 18px; line-height: 1.25; font-weight: 400;
  }
  .offer__url { margin-top: 8px; font-size: 20px; font-weight: 700; }
  .offer__notes {
    position: absolute; left: 28px; right: 28px; bottom: 26px; height: 120px;
    background: var(--white); border-radius: 22px;
    padding: 40px 32px 0;
  }
  .offer__line { height: 1px; background: var(--rule); margin-bottom: 36px; }

  /* Identity side */
  .card--identity { top: 470px; background: var(--white); }
  .identity__swoosh { position: absolute; inset: 0; }
  .identity__brand {
    position: absolute; left: 0; right: 0; top: 82px;
    display: flex; flex-direction: column; align-items: center;
  }
  .identity__wordmark { display: flex; align-items: center; gap: 14px; }
  .identity__dot { width: 34px; height: 34px; border-radius: 50%; background: var(--orange); }
  .identity__name {
    font-weight: 800; font-size: 62px; letter-spacing: 1px; color: var(--ink);
    text-transform: uppercase; line-height: 1;
  }
  .identity__tagline {
    margin-top: 8px; font-weight: 700; font-size: 15px; letter-spacing: 2px;
    text-transform: uppercase; color: var(--ink);
  }
  .identity__contact {
    position: absolute; right: 60px; bottom: 42px; text-align: center; color: var(--white);
  }
  .contact__name { font-weight: 800; font-size: 24px; text-transform: uppercase; line-height: 1.1; }
  .contact__role { font-weight: 700; font-size: 19px; text-transform: uppercase; line-height: 1.2; }
  .contact__email { font-weight: 400; font-size: 17px; }
</style>
</head>
<body>

<section class="card card--offer">
  <div class="offer__brand">
    <div class="offer__dot"></div>
    <div class="offer__name">Larkwell</div>
  </div>
  <div class="offer__divider"></div>
  <div class="offer__copy">
    <h1 class="offer__headline">Widen your circle.<br>Grow your revenue.<br>Leave a lasting mark.</h1>
    <p class="offer__text">Claim your free Larkwell welcome kit and our online growth playbook now at</p>
    <p class="offer__url">Larkwellnow.com/start</p>
  </div>
  <div class="offer__notes">
    <div class="offer__line"></div>
    <div class="offer__line"></div>
  </div>
</section>

<section class="card card--identity">
  <svg class="identity__swoosh" viewBox="0 0 700 400" width="700" height="400" aria-hidden="true">
    <defs>
      <linearGradient id="swooshFill" x1="0" y1="0" x2="1" y2="1">
        <stop offset="0" stop-color="#f8963a"/>
        <stop offset="1" stop-color="#e85d1c"/>
      </linearGradient>
    </defs>
    <path d="M0 296 C180 210 300 330 470 250 C560 208 630 190 700 188 L700 400 L0 400 Z" fill="#1c1c1c"/>
    <path d="M0 308 C180 224 300 344 470 264 C560 222 630 204 700 202 L700 400 L0 400 Z" fill="url(#swooshFill)"/>
  </svg>
  <div class="identity__brand">
    <div class="identity__wordmark">
      <div class="identity__dot"></div>
      <div class="identity__name">Larkwell</div>
    </div>
    <div class="identity__tagline">Marketing that moves people forward</div>
  </div>
  <div class="identity__contact">
    <div class="contact__name">Dana Whitfield</div>
    <div class="contact__role">Story Marketing Coach</div>
    <div class="contact__email">dana@larkwellnow.com</div>
  </div>
</section>

</body>
</html>
```